Federal IT Consulting Company - Brisolux Consulting Group

We're seeking a skilled web designer to create a modern, bold, and engaging WordPress website for Brisolux Consulting Group, LLC. Our company specializes in federal IT consulting, and our name is a play on "Brightening Solutions." The website should reflect our expertise in the federal technology marketplace and position us as a trusted partner for clients navigating their IT journey.

contact: info@brisoluxgrp-example.com

Current Status

WordPress is already installed on our hosting account
We have an existing logo (may need modernization)

Design Requirements

Style:

Modern and visually striking design
Bold elements to convey confidence and expertise
Incorporate the concept of "brightening solutions" into the design

Features:

Modern UX sliders for dynamic content presentation
Eye-catching, high-quality images (stock photos to be sourced by the designer)
Responsive design for all devices

Color Scheme:

To be proposed by the designer, should align with our brand and convey trust and technological expertise

Logo:

Evaluate our current logo
Create a transparent background version if needed
Propose modernization if deemed necessary

Accessibility:

Ensure design elements are accessible to users with disabilities
Use high contrast ratios for text and background colors
Provide text alternatives for non-text content

Website Structure
Create the following pages, with the possibility of subpages:

Home
Services
About
Contact

Specific Page Requirements
Home Page

Striking hero section with a clear value proposition
Overview of our services
Client testimonials or trust indicators

Services Page

Detailed list of our IT consulting services
Clear explanation of how we help navigate the federal IT landscape

About Page

Company history and mission
Team highlights (if applicable)
Our approach to federal IT consulting

Contact Page

Contact form
Other contact methods (phone, email)

Technical Requirements

Fully responsive design
SEO best practices implemented
Fast loading times
Integration with necessary plugins (to be discussed)
Training on how to update and maintain the site
Full compliance with Web Content Accessibility Guidelines (WCAG) 2.1 Level AA
Adherence to Section 508 standards for federal website accessibility
Implementation of necessary features for ADA compliance
Updates

Designs look the same

Target Market(s)

US Federal Govt customers looking for IT support.

Industry/Entity Type

IT Consulting

Coding

Coded - Design and coding required

Colors
0054AA
0677BA
7BADD7
CADEEF
E8F1F8
0094D4
00A9DD
6FCCEA
C7EBF8
E9F6FB
00AB8E
00BBA5
67D7C9
C6EFE9
E9F9F6

```html
<!DOCTYPE html>
<html lang="en">
<head>
<meta charset="utf-8">
<title>Brisolux Consulting Group — Federal IT Consulting</title>
<link rel="stylesheet" href="https://fonts.googleapis.com/css2?family=Michroma&family=Outfit:wght@300;400;500;600;700&family=Montserrat:wght@600&display=swap">
<style>
:root{
  --blue-deep:#0054AA;
  --blue:#0677BA;
  --blue-bright:#00A9DD;
  --blue-soft:#7BADD7;
  --blue-pale:#CADEEF;
  --blue-mist:#E8F1F8;
  --navy:#0c2c55;
  --navy-footer:#0b2446;
  --slate:#2b4a70;
  --ink:#111a27;
  --text:#3a4250;
  --muted:#7b8494;
  --white:#ffffff;
  --star:#f5a623;
}
*{box-sizing:border-box;margin:0;padding:0}
html,body{width:1200px;height:4021px;overflow:hidden}
body{position:relative;background:var(--white);font-family:"Outfit",sans-serif;color:var(--ink)}
.abs{position:absolute}
a{color:inherit;text-decoration:none}

/* header */
.site-header{position:absolute;left:0;top:0;width:1200px;height:69px;background:var(--white)}
.brand{position:absolute;display:flex;align-items:center;gap:9px;font-family:"Outfit",sans-serif;font-weight:700;letter-spacing:2px}
.brand .dot{width:26px;height:26px;border-radius:50%;background:var(--blue)}
.site-header .brand{left:142px;top:17px;font-size:26px;color:var(--navy)}
.main-nav a{position:absolute;top:29px;font-size:13px;color:var(--text)}
.main-nav a.current{color:var(--blue);font-weight:600}
.btn{position:absolute;display:flex;align-items:center;justify-content:center;gap:8px;border-radius:40px;font-size:13px;font-weight:500}
.btn-primary{background:var(--blue);color:var(--white);box-shadow:0 6px 14px rgba(6,119,186,.28)}
.btn-light{background:var(--white);color:var(--text)}

/* hero */
.hero{position:absolute;left:0;top:69px;width:1200px;height:529px;overflow:hidden}
.hero-image{position:absolute;inset:0;background:linear-gradient(90deg,#eef3f8 0%,#e3ecf5 35%,#b9d0e6 55%,#c9d6e3 72%,#6f7e6a 100%)}
.hero-image::after{content:"";position:absolute;left:0;right:0;bottom:0;height:140px;background:linear-gradient(180deg,rgba(80,96,80,0),rgba(70,86,66,.55))}
.hero-title{position:absolute;left:142px;top:99px;font-family:"Michroma",sans-serif;font-size:40px;line-height:48.5px;color:var(--ink);text-transform:uppercase}
.hero-sub{position:absolute;left:142px;top:302px;font-family:"Montserrat",sans-serif;font-weight:600;font-size:16px;line-height:24px;letter-spacing:3.2px;text-transform:uppercase;color:var(--ink)}

/* shared section heads */
.eyebrow{position:absolute;font-size:12px;font-weight:500;letter-spacing:.6px;color:var(--blue);padding-left:9px;border-left:2px solid var(--blue);line-height:15px;text-transform:uppercase}
.section-title{position:absolute;font-size:28px;font-weight:600;line-height:36px;color:var(--ink)}
.section-title em{font-style:normal;color:var(--blue-bright)}
.center{left:0;width:1200px;text-align:center}
.eyebrow.center{left:50%;width:auto;transform:translateX(-50%)}

/* about */
.about-copy{position:absolute;left:142px;width:440px;font-size:12.5px;line-height:22.6px;color:var(--text)}
.about-visual{position:absolute;left:664px;top:692px;width:390px;height:390px;border-radius:50%;background:radial-gradient(circle at 50% 45%,#d7dfe7 0%,#9fb3c6 55%,#2e3c4e 88%,#1a2433 100%)}

/* services */
.services-photo{position:absolute;left:0;top:1314px;width:421px;height:342px;border-radius:0 16px 16px 0;background:linear-gradient(135deg,#8a7a66 0%,#c7c0b4 40%,#5c5247 75%,#3a342d 100%)}
.round-btn{position:absolute;width:38px;height:38px;border-radius:50%;display:flex;align-items:center;justify-content:center}
.round-btn.outline{border:1.5px solid var(--blue);background:var(--white)}
.round-btn.fill{background:var(--blue-bright)}
.service-card{position:absolute;top:1378px;width:212px;height:215px;background:var(--white);border-radius:12px;box-shadow:0 6px 24px rgba(20,40,80,.12);padding:22px 21px}
.service-card .icon{width:56px;height:56px;border-radius:10px;background:var(--blue-deep);display:flex;align-items:center;justify-content:center}
.service-card h3{margin-top:22px;font-size:16px;font-weight:500;color:var(--ink)}
.service-card p{margin-top:9px;font-size:12.5px;line-height:19px;color:var(--text);width:170px}
.service-card .go{position:absolute;right:10px;bottom:10px;width:27px;height:27px;border-radius:50%;background:var(--blue-bright);display:flex;align-items:center;justify-content:center}

/* testimonials */
.testimonials{position:absolute;left:0;top:1741px;width:1200px;height:519px;background:var(--navy)}
.testimonials .eyebrow{color:var(--white);border-color:var(--white)}
.testimonials .section-title{color:var(--white)}
.testi-photo{position:absolute;left:601px;top:116px;width:370px;height:258px;border-radius:8px;background:linear-gradient(135deg,#c9ced4 0%,#8b97a5 40%,#4d5a6a 75%,#a2abb6 100%)}
.testi-panel{position:absolute;left:866px;top:295px;width:192px;height:167px;border-radius:12px;background:var(--slate)}
.testi-card{position:absolute;left:259px;top:233px;width:370px;height:226px;background:var(--white);border-radius:10px;padding:22px}
.avatar{width:56px;height:56px;border-radius:50%;background:linear-gradient(160deg,#e9d6cc,#9c5a4a)}
.stars{position:absolute;right:22px;top:30px;display:flex;gap:3px}
.testi-card h4{margin-top:16px;font-size:13px;font-weight:600}
.testi-card .role{margin-top:6px;font-size:10px;color:var(--muted)}
.testi-card p{margin-top:12px;font-size:10.5px;line-height:20.5px;color:var(--text)}
.dot-grid{position:absolute;left:978px;top:1901px;display:grid;grid-template-columns:repeat(3,4px);gap:14px 14px}
.dot-grid span{width:3px;height:3px;border-radius:50%;background:var(--blue-bright)}

/* team */
.member{position:absolute;top:2457px;width:182px;text-align:center}
.member .portrait{width:182px;height:182px;border-radius:50%;background:linear-gradient(180deg,#e6eef7 0%,#cfdff0 60%,#8aa7c6 100%)}
.member h4{margin-top:24px;font-size:15px;font-weight:600}
.member .role{margin-top:6px;font-size:11px;color:var(--blue-bright)}
.member .social{margin-top:10px;display:flex;justify-content:center;gap:11px}
.member .social span{width:30px;height:30px;border-radius:50%;background:var(--blue-bright)}

/* cta */
.cta{position:absolute;left:142px;top:2863px;width:916px;height:328px;border-radius:48px;background:linear-gradient(100deg,#0a4fa6 0%,#0657b8 60%,#0a63c4 100%)}
.cta-person{position:absolute;left:671px;top:2801px;width:265px;height:390px;border-radius:130px 130px 0 0;background:linear-gradient(180deg,#c99c7a 0%,#d9c3a8 35%,#c4a88a 70%,#8f7a66 100%)}
.cta h2{position:absolute;left:198px;top:2913px;font-size:26px;font-weight:500;line-height:43px;color:var(--white)}
.cta-copy{position:absolute;left:198px;top:3018px;font-size:13px;line-height:22px;color:var(--white);width:440px}
.btn-white{background:var(--white);color:var(--blue-deep);font-weight:600}

/* certificates */
.cert{position:absolute;top:3419px;height:180px}
.cert-a{left:197px;width:252px;background:linear-gradient(135deg,#fbf3e7,#ead6b8);border:3px solid #c98a4a}
.cert-b{left:481px;width:240px;background:linear-gradient(135deg,#1d3557 0%,#e7ebf1 30%,#f4f5f7 70%,#d4b24c 100%)}
.cert-c{left:752px;width:251px;background:linear-gradient(100deg,#152b4a 0%,#c7a23a 22%,#f2f3f5 35%,#eef0f3 100%)}
.round-btn.ring{border:1.5px solid var(--blue);background:var(--white);width:34px;height:34px}
.round-btn.solid{background:var(--blue-deep);width:34px;height:34px}

/* footer */
.site-footer{position:absolute;left:0;top:3686px;width:1200px;height:335px;background:linear-gradient(180deg,#0c2a4f,#0a2142)}
.site-footer .brand{left:142px;top:80px;font-size:40px;color:var(--white);gap:14px}
.site-footer .brand .dot{width:40px;height:40px;background:var(--blue-bright)}
.foot-col{position:absolute;top:80px}
.foot-col h5{font-size:15px;font-weight:500;color:var(--blue-bright)}
.foot-col li{list-style:none;font-size:12px;color:var(--white);margin-top:12px}
.contact-row{display:flex;gap:10px;align-items:flex-start;font-size:12px;line-height:17px;color:var(--white);margin-top:12px}
.contact-row svg{flex:none;margin-top:1px}
.copyright{position:absolute;left:142px;top:290px;font-size:11.5px;color:var(--white)}
.foot-social{position:absolute;left:909px;top:285px;display:flex;gap:10px}
.foot-social span{width:30px;height:30px;border-radius:50%;background:var(--blue-bright)}
</style>
</head>
<body>

<header class="site-header">
  <a class="brand" href="#"><span class="dot"></span>BRISOLUX</a>
  <nav class="main-nav">
    <a class="current" href="#" style="left:601px">Home</a>
    <a href="#" style="left:701px">About Us</a>
    <a href="#" style="left:823px">Services</a>
  </nav>
  <a class="btn btn-primary" href="#" style="left:936px;top:19px;width:122px;height:37px">Contact Us</a>
</header>

<section class="hero">
  <div class="hero-image" role="img" aria-label="Photo of the US Capitol building under a bright blue sky framed by trees"></div>
  <h1 class="hero-title">Navigate Your<br>Federal IT<br>Journey With<br>Confidence</h1>
  <p class="hero-sub">Expert Consulting Services To<br>Guide Your IT Strategy</p>
  <a class="btn btn-primary" href="#" style="left:142px;top:368px;width:178px;height:42px">Explore Our Services</a>
  <a class="btn btn-light" href="#" style="left:332px;top:368px;width:181px;height:42px">Get A Free Consultation</a>
</section>

<section class="about">
  <span class="eyebrow" style="left:142px;top:722px">About Us</span>
  <h2 class="section-title" style="left:142px;top:750px">Why Choose <em>Brisolux?</em></h2>
  <p class="about-copy" style="top:809px">There are many variations of passages of Lorem Ipsum available, but the majority have suffered alteration in some form, by injected humour, or randomised words which don't look even slightly believable. If you are going to use a passage of Lorem Ipsum, you need to be sure there isn't anything embarrassing hidden in the middle of text.</p>
  <p class="about-copy" style="top:936px">It is a long established fact that a reader will be distracted by the readable content of a page when looking at its layout.</p>
  <a class="btn btn-primary" href="#" style="left:142px;top:1007px;width:128px;height:42px">Learn More
    <svg width="11" height="11" viewBox="0 0 11 11"><path d="M2 9L9 2M3.5 2H9V7.5" fill="none" stroke="#fff" stroke-width="1.4"/></svg></a>
  <div class="about-visual" role="img" aria-label="Photo of a smiling consultant working at a desk, set in a circular frame"></div>
</section>

<section class="services">
  <span class="eyebrow" style="left:142px;top:1173px">Popular Services</span>
  <h2 class="section-title" style="left:142px;top:1201px">The Best Solution For<br>Your <em>Business</em></h2>
  <div class="services-photo" role="img" aria-label="Photo of a consulting team gathered around a computer in an office"></div>
  <a class="round-btn outline" href="#" aria-label="Previous" style="left:956px;top:1306px">
    <svg width="16" height="12" viewBox="0 0 16 12"><path d="M15 6H2M6.5 1.5L2 6l4.5 4.5" fill="none" stroke="#0677BA" stroke-width="1.6"/></svg></a>
  <a class="round-btn fill" href="#" aria-label="Next" style="left:1019px;top:1306px">
    <svg width="16" height="12" viewBox="0 0 16 12"><path d="M1 6h13M9.5 1.5L14 6l-4.5 4.5" fill="none" stroke="#fff" stroke-width="1.6"/></svg></a>

  <article class="service-card" style="left:378px">
    <div class="icon"><svg width="30" height="30" viewBox="0 0 30 30" fill="none" stroke="#fff" stroke-width="1.5"><path d="M15 5l8 3v6c0 5-3.5 8.5-8 10-4.5-1.5-8-5-8-10V8z"/><rect x="12" y="13" width="6" height="5"/><path d="M13.3 13v-1.6a1.7 1.7 0 013.4 0V13"/></svg></div>
    <h3>Cybersecurity</h3>
    <p>There are many variations of passages of Lorem Ipsum available.</p>
    <span class="go"><svg width="10" height="10" viewBox="0 0 10 10"><path d="M2 8L8 2M3 2h5v5" fill="none" stroke="#fff" stroke-width="1.4"/></svg></span>
  </article>
  <article class="service-card" style="left:612px">
    <div class="icon"><svg width="30" height="30" viewBox="0 0 30 30" fill="none" stroke="#fff" stroke-width="1.5"><path d="M9 14a4 4 0 01.8-7.9A6 6 0 0121 8a3.5 3.5 0 01.5 6.9z"/><rect x="10" y="16" width="10" height="3"/><rect x="10" y="20" width="10" height="3"/><path d="M15 23v3"/></svg></div>
    <h3>Cloud Services</h3>
    <p>There are many variations of passages of Lorem Ipsum available.</p>
    <span class="go"><svg width="10" height="10" viewBox="0 0 10 10"><path d="M2 8L8 2M3 2h5v5" fill="none" stroke="#fff" stroke-width="1.4"/></svg></span>
  </article>
  <article class="service-card" style="left:846px">
    <div class="icon"><svg width="30" height="30" viewBox="0 0 30 30" fill="none" stroke="#fff" stroke-width="1.5"><circle cx="15" cy="9" r="3"/><path d="M10 17a5 5 0 0110 0"/><rect x="6" y="19" width="18" height="6"/><path d="M4 25h22"/></svg></div>
    <h3>IT Strategy Consulting</h3>
    <p>There are many variations of passages of Lorem Ipsum available.</p>
    <span class="go"><svg width="10" height="10" viewBox="0 0 10 10"><path d="M2 8L8 2M3 2h5v5" fill="none" stroke="#fff" stroke-width="1.4"/></svg></span>
  </article>
</section>

<section class="testimonials">
  <span class="eyebrow" style="left:142px;top:117px">Our Testimonials</span>
  <h2 class="section-title" style="left:142px;top:145px">Hear What Our <em>Clients Say</em></h2>
  <div class="testi-photo" role="img" aria-label="Photo of a presenter leading a meeting with colleagues at laptops"></div>
  <div class="testi-panel"></div>
  <a class="round-btn" href="#" aria-label="Previous" style="left:944px;top:404px;border:1.5px solid #fff">
    <svg width="16" height="12" viewBox="0 0 16 12"><path d="M15 6H2M6.5 1.5L2 6l4.5 4.5" fill="none" stroke="#fff" stroke-width="1.5"/></svg></a>
  <a class="round-btn" href="#" aria-label="Next" style="left:1000px;top:404px;background:#fff">
    <svg width="16" height="12" viewBox="0 0 16 12"><path d="M1 6h13M9.5 1.5L14 6l-4.5 4.5" fill="none" stroke="#0c2c55" stroke-width="1.5"/></svg></a>
  <article class="testi-card">
    <div class="avatar" role="img" aria-label="Portrait of the client"></div>
    <div class="stars" aria-label="5 out of 5 stars">
      <svg width="80" height="14" viewBox="0 0 80 14" fill="#f5a623"><g id="s"><path d="M7 0l2 4.6 5 .5-3.8 3.3 1.1 4.9L7 10.8 2.7 13.3l1.1-4.9L0 5.1l5-.5z"/></g><use href="#s" x="16.5"/><use href="#s" x="33"/><use href="#s" x="49.5"/><use href="#s" x="66"/></svg>
    </div>
    <h4>Elias R. Danforth</h4>
    <div class="role">CEO &amp; Founder</div>
    <p>It is a long established fact that a reader will be distracted by the readable content of a page when looking at its layout. The point of using Lorem Ipsum is that it has a more-or-less normal distribution.</p>
  </article>
</section>
<div class="dot-grid"><span></span><span></span><span></span><span></span><span></span><span></span><span></span><span></span><span></span><span></span><span></span><span></span></div>

<section class="team">
  <span class="eyebrow center" style="top:2345px">Our Team</span>
  <h2 class="section-title center" style="top:2374px">Meet The Our <em>Experts</em></h2>
  <div class="member" style="left:174px"><div class="portrait" role="img" aria-label="Portrait of Mara Quell"></div><h4>Mara Quell</h4><div class="role">Web Designer</div><div class="social"><span></span><span></span></div></div>
  <div class="member" style="left:397px"><div class="portrait" role="img" aria-label="Portrait of Tobin Ardley"></div><h4>Tobin Ardley</h4><div class="role">Web Designer</div><div class="social"><span></span><span></span></div></div>
  <div class="member" style="left:619px"><div class="portrait" role="img" aria-label="Portrait of Lena Vorsch"></div><h4>Lena Vorsch</h4><div class="role">Web Designer</div><div class="social"><span></span><span></span></div></div>
  <div class="member" style="left:842px"><div class="portrait" role="img" aria-label="Portrait of Caleb Wynd"></div><h4>Caleb Wynd</h4><div class="role">Web Designer</div><div class="social"><span></span><span></span></div></div>
</section>

<section>
  <div class="cta"></div>
  <div class="cta-person" role="img" aria-label="Photo of a smiling consultant in a beige suit holding a laptop"></div>
  <h2 class="cta h2" style="position:absolute;left:198px;top:2913px;font-size:26px;font-weight:500;line-height:43px;color:#fff;background:none;width:auto;height:auto;border-radius:0">We Are Federal IT Consulting<br>We Make Future!</h2>
  <p class="cta-copy">There are many variations of passages of Lorem Ipsum available, but the majority have suffered alteration in some form.</p>
  <a class="btn btn-white" href="#" style="left:198px;top:3099px;width:187px;height:41px">Explore Our Services
    <svg width="11" height="11" viewBox="0 0 11 11"><path d="M2 9L9 2M3.5 2H9V7.5" fill="none" stroke="#0054AA" stroke-width="1.4"/></svg></a>
  <svg class="abs" style="left:405px;top:3067px" width="130" height="90" viewBox="0 0 130 90" fill="none" stroke="#cfe0f5" stroke-width="1.2">
    <path d="M120 6L96 16l10 4 4 9z"/>
    <path d="M96 22c-20 10-40 8-50 12-12 5-8 16-20 18-10 2-8 14-12 30" stroke-dasharray="4 4"/>
  </svg>
</section>

<section class="certificates">
  <span class="eyebrow center" style="top:3278px">Certifications</span>
  <h2 class="section-title center" style="top:3306px">Certificates Of The Most<br>Popular <em>Brands</em></h2>
  <a class="round-btn ring" href="#" aria-label="Previous" style="left:141px;top:3493px">
    <svg width="8" height="12" viewBox="0 0 8 12"><path d="M6.5 1L1.5 6l5 5" fill="none" stroke="#0677BA" stroke-width="1.6"/></svg></a>
  <div class="cert cert-a" role="img" aria-label="Certificate of achievement with gold border"></div>
  <div class="cert cert-b" role="img" aria-label="Certificate with navy and gold corners"></div>
  <div class="cert cert-c" role="img" aria-label="Certificate of achievement with navy side band"></div>
  <a class="round-btn solid" href="#" aria-label="Next" style="left:1024px;top:3493px">
    <svg width="8" height="12" viewBox="0 0 8 12"><path d="M1.5 1l5 5-5 5" fill="none" stroke="#fff" stroke-width="1.6"/></svg></a>
</section>

<footer class="site-footer">
  <a class="brand" href="#"><span class="dot"></span>BRISOLUX</a>
  <div class="foot-col" style="left:512px"><h5>Quick Links</h5><ul><li>Home</li><li>About Us</li><li>Services</li></ul></div>
  <div class="foot-col" style="left:674px"><h5>Resources</h5><ul><li>Privacy Policy</li><li>Terms Of Service</li></ul></div>
  <div class="foot-col" style="left:852px;width:210px">
    <h5>Contact Info</h5>
    <div class="contact-row"><svg width="14" height="16" viewBox="0 0 14 16"><path d="M7 15s5-5 5-8.5A5 5 0 002 6.5C2 10 7 15 7 15z" fill="none" stroke="#00A9DD" stroke-width="1.5"/><circle cx="7" cy="6.5" r="1.8" fill="#00A9DD"/></svg><span>48 Harbor Crest Way, #210<br>Ledger Road 5521</span></div>
    <div class="contact-row" style="margin-top:16px"><svg width="15" height="12" viewBox="0 0 15 12"><rect width="15" height="12" rx="1.5" fill="#00A9DD"/><path d="M1 1.5l6.5 5 6.5-5" fill="none" stroke="#0b2446" stroke-width="1.2"/></svg><span>hello@brisolux-example.com</span></div>
    <div class="contact-row" style="margin-top:16px"><svg width="14" height="14" viewBox="0 0 14 14"><path d="M3 1l2.5 3-1.5 1.5c1 2 2.5 3.5 4.5 4.5L10 8.5l3 2.5-1.5 2.5C6 13 1 8 .5 2.5z" fill="#00A9DD"/></svg><span>555-014-2290</span></div>
  </div>
  <p class="copyright">© 2024 Brisolux. All rights reserved.</p>
  <div class="foot-social" aria-label="Social media links"><span></span><span></span><span></span><span></span></div>
</footer>

</body>
</html>
```